Talvique Hotels Business Card and Logo

We need a business card design for a hotel group. I saw a hotel card you designed and really liked it. We have multiple properties with different brands. Were hoping that the card would be unique and find a way to list out all our properties. Our web address is www.talviquehotels.com. I have attached some photos of card designs I like.

Industry/Entity Type

Hotel

Contact Information for Business Card

Scott CurranReneson HotelsChief Operating Officer56 Madera DriveCorte Madera, CA 94925Office 415-891-5013Cell 707-5550143

```html
<!DOCTYPE html>
<html lang="en">
<head>
<meta charset="utf-8">
<title>Talvique Hotels Business Card</title>
<link href="https://fonts.googleapis.com/css2?family=Montserrat:wght@400;500;600&display=swap" rel="stylesheet">
<style>
  :root {
    --navy: #123a66;
    --navy-deep: #0d2f57;
    --green: #7cc242;
    --grey-text: #555b63;
    --page: #d9dadc;
    --card: #ffffff;
    --photo-top: #3c6b8a;
    --photo-mid: #2c7d92;
    --photo-low: #3f6c86;
  }
  * { margin: 0; padding: 0; box-sizing: border-box; }
  html, body { width: 1200px; height: 930px; overflow: hidden; background: var(--page); }
  .canvas { position: relative; width: 1200px; height: 930px; }
  .card {
    position: absolute; width: 740px; height: 423px; border-radius: 22px;
    overflow: hidden; box-shadow: 0 6px 18px rgba(0,0,0,.18);
  }
  .card-front { left: 230px; top: 22px; }
  .card-back { left: 230px; top: 485px; background: var(--card); }

  .front-photo {
    position: absolute; inset: 0;
    background: linear-gradient(160deg, var(--photo-top) 0%, var(--photo-mid) 55%, var(--photo-low) 100%);
  }
  .front-name {
    position: absolute; left: 0; right: 0; top: 184px; text-align: center;
    font-family: 'Montserrat', sans-serif; font-weight: 500; font-size: 40px;
    letter-spacing: 4px; color: #ffffff;
  }

  .back-name {
    position: absolute; left: 40px; top: 118px;
    font-family: 'Montserrat', sans-serif; font-weight: 500; font-size: 25px;
    letter-spacing: 2px; color: var(--navy);
  }
  .person { position: absolute; right: 40px; top: 82px; text-align: right; font-family: 'Montserrat', sans-serif; }
  .person-name { font-weight: 600; font-size: 24px; color: var(--navy); letter-spacing: -.3px; }
  .person-title { font-size: 14px; color: var(--grey-text); margin-top: 2px; }
  .edge-tab { position: absolute; right: 0; top: 80px; width: 12px; height: 36px; background: var(--green); }
  .rule { position: absolute; height: 1.5px; background: var(--green); }
  .rule-top { left: 400px; right: 40px; top: 150px; }
  .rule-bottom { left: 40px; width: 300px; top: 292px; }
  .address {
    position: absolute; right: 40px; top: 170px; text-align: right;
    font-family: 'Montserrat', sans-serif; font-size: 16px; line-height: 24px; color: var(--grey-text);
  }
  .contacts {
    position: absolute; left: 40px; top: 302px; list-style: none;
    font-family: 'Montserrat', sans-serif; font-size: 16px; line-height: 21px; color: var(--grey-text);
  }
  .contacts li { display: flex; align-items: center; gap: 8px; }
  .contacts svg { width: 12px; height: 12px; flex: none; }
  .wave { position: absolute; left: 0; bottom: 0; width: 740px; height: 423px; }
</style>
</head>
<body>
<div class="canvas">
  <section class="card card-front">
    <div class="front-photo" role="img" aria-label="Hotel courtyard with swimming pool, lounge chairs and buildings, tinted in deep blue"></div>
    <div class="front-name">TALVIQUE HOTELS</div>
  </section>

  <section class="card card-back">
    <svg class="wave" viewBox="0 0 740 423" aria-hidden="true">
      <path d="M0,423 C300,418 480,305 740,252 L740,264 C480,318 300,423 0,423 Z" fill="var(--green)"/>
      <path d="M0,423 C300,423 480,326 740,272 L740,423 Z" fill="var(--navy-deep)"/>
    </svg>
    <div class="back-name">TALVIQUE HOTELS</div>
    <div class="edge-tab"></div>
    <div class="person">
      <div class="person-name">Brent Holloway Talvique</div>
      <div class="person-title">Hotels Chief Operating Officer</div>
    </div>
    <div class="rule rule-top"></div>
    <div class="address">83 Pellwick Lane<br>Larkmoor, CA 94917</div>
    <div class="rule rule-bottom"></div>
    <ul class="contacts">
      <li><svg viewBox="0 0 12 12"><path d="M2 1l2 0 1 3-1.5 1a6 6 0 0 0 3 3L8 7l3 1v2l-1 1C5 11 1 7 1 2z" fill="var(--green)"/></svg>415-555-0186</li>
      <li><svg viewBox="0 0 12 12"><rect x="3" y="1" width="6" height="10" rx="1" fill="none" stroke="var(--green)" stroke-width="1.4"/></svg>707-5550143</li>
      <li><svg viewBox="0 0 12 12"><rect x="1" y="2.5" width="10" height="7" fill="none" stroke="var(--green)" stroke-width="1.3"/><path d="M1 2.5l5 4 5-4" fill="none" stroke="var(--green)" stroke-width="1.3"/></svg>info@talviquehotels.com</li>
      <li><svg viewBox="0 0 12 12"><circle cx="6" cy="6" r="4.8" fill="none" stroke="var(--green)" stroke-width="1.2"/><path d="M1.2 6h9.6M6 1.2c-2.4 3-2.4 6.6 0 9.6M6 1.2c2.4 3 2.4 6.6 0 9.6" fill="none" stroke="var(--green)" stroke-width="1"/></svg>www.talviquehotels.com</li>
    </ul>
  </section>
</div>
</body>
</html>
```